Automotive component supplier needs a business card design

We need a business card design for our company called Velran Global Components Ltd based in the UK. We are a supplier of interior and exterior components to premium car manufacturers such as Corvel Ashby, Hadley Fenn, Marquist and Tavarelli. We would like to see a modern business card design that uses the colour blue.

Target Market(s)

Premium automotive car manufacturers.

Industry/Entity Type

Automotive

Contact Information for Business Card

Company Name : Velran Global Components Limited
Address: 17 Marlow Yard, Upper Heath, Warwick, CV31 8QL, United Kingdom
Web Address : www.velrancomponents-example.co.uk

Font styles to use
Other font styles liked:
• Helvetica

Colors
3176b5
0255a3
85acd3
cfdeed
cee9f5
85cae6
34a6d7
0692cd
9bcb3c

Requirements
Must have
• Clear company logo and a mixture of blue colours.
Nice to have
• A high quality modern image.
Should not have
• Multiple colours.

```html
<!DOCTYPE html>
<html lang="en">
<head>
<meta charset="utf-8">
<title>Velran Global Components – Business Card</title>
<link rel="stylesheet" href="https://fonts.googleapis.com/css2?family=Lato:wght@400;700;900&display=swap">
<style>
  :root {
    --stage: #3b3c3f;
    --card-blue: #0a8bd0;
    --deep-blue: #0692cd;
    --lime: #9bcb3c;
    --white: #ffffff;
    --paper: #ffffff;
  }
  * { margin: 0; padding: 0; box-sizing: border-box; }
  html, body { width: 1200px; height: 800px; overflow: hidden; }
  body {
    background: var(--stage);
    font-family: "Lato", Helvetica, Arial, sans-serif;
    position: relative;
  }
  .card {
    position: absolute;
    width: 530px;
    height: 303px;
    top: 248px;
    overflow: hidden;
    border-radius: 2px;
    box-shadow: 0 14px 30px rgba(0,0,0,.45);
  }
  /* Front */
  .card--front { left: 40px; background: var(--card-blue); color: var(--white); }
  .brand {
    display: flex;
    align-items: center;
    gap: 10px;
    font-weight: 900;
    letter-spacing: .5px;
    white-space: nowrap;
  }
  .brand__mark { width: 14px; height: 14px; background: var(--lime); flex: none; }
  .card--front .brand {
    position: absolute;
    left: 50%; top: 104px;
    transform: translateX(-50%);
    font-size: 31px;
    color: var(--white);
  }
  .card--front .front-web {
    position: absolute;
    left: 0; right: 0; bottom: 46px;
    text-align: center;
    font-size: 12.5px;
    letter-spacing: 1.6px;
  }
  /* Back */
  .card--back { left: 630px; background: var(--paper); }
  .card--back .wave { position: absolute; inset: 0; }
  .card--back .brand {
    position: absolute;
    left: 30px; top: 48px;
    font-size: 27px;
    color: var(--deep-blue);
  }
  .contact-list {
    position: absolute;
    left: 30px; bottom: 22px;
    list-style: none;
    color: var(--white);
    font-size: 13px;
    line-height: 19px;
  }
  .contact-list li { display: flex; align-items: center; gap: 10px; }
  .contact-list svg { width: 12px; height: 12px; flex: none; }
  .person {
    position: absolute;
    left: 300px; top: 150px;
    color: var(--white);
  }
  .person__name { font-size: 19px; font-weight: 700; color: var(--lime); line-height: 22px; }
  .person__role { font-size: 13px; margin-top: 2px; }
  .person__address { font-size: 13px; line-height: 18px; margin-top: 16px; font-style: normal; }
</style>
</head>
<body>

<section class="card card--front">
  <div class="brand"><span class="brand__mark"></span>Velran Global Components</div>
  <p class="front-web">www.velrancomponents-example.co.uk</p>
</section>

<section class="card card--back">
  <svg class="wave" viewBox="0 0 530 303" preserveAspectRatio="none" aria-hidden="true">
    <path fill="var(--lime)" d="M0,176 C120,176 210,170 290,118 S440,48 530,40 L530,303 L0,303 Z"/>
    <path fill="var(--white)" d="M0,188 C120,188 210,182 290,130 S440,60 530,52 L530,303 L0,303 Z"/>
    <path fill="var(--card-blue)" d="M0,192 C120,192 210,186 290,134 S440,64 530,56 L530,303 L0,303 Z"/>
  </svg>

  <div class="brand"><span class="brand__mark"></span>Velran Global Components</div>

  <div class="person">
    <p class="person__name">Marcus Tellby</p>
    <p class="person__role">Manager</p>
    <address class="person__address">17 Marlow Yard, Upper Heath<br>Warwick, CV31 8QL<br>United Kingdom</address>
  </div>

  <ul class="contact-list">
    <li>
      <svg viewBox="0 0 12 12"><path fill="var(--lime)" d="M2.5 0.8 4.3 3 3.4 4.3c.7 1.6 2.1 3 3.7 3.7l1.3-.9 2.2 1.8-.9 2C5.3 11 .6 6.4.5 1.7z"/></svg>
      512 004 7300
    </li>
    <li>
      <svg viewBox="0 0 12 12"><rect x="3" y="0.5" width="6" height="11" rx="1" fill="var(--lime)"/><rect x="4" y="2" width="4" height="6" fill="var(--card-blue)"/></svg>
      512 004 7301
    </li>
    <li>
      <svg viewBox="0 0 12 12"><rect x="0.5" y="2" width="11" height="8" fill="var(--lime)"/><path d="M0.5 2 6 6.5 11.5 2" fill="none" stroke="var(--card-blue)" stroke-width="1"/></svg>
      info@velrancomponents-example.co.uk
    </li>
    <li>
      <svg viewBox="0 0 12 12"><circle cx="6" cy="6" r="5.5" fill="var(--lime)"/><path d="M0.5 6h11M6 .5v11M2 3h8M2 9h8" stroke="var(--card-blue)" stroke-width=".8" fill="none"/></svg>
      www.velrancomponents-example.co.uk
    </li>
  </ul>
</section>

</body>
</html>
```